Vantro cards

I am in the auto motive, transportation business I would like a business card that is Something cool, modern edgy, having to do with car culture. I offer towing service for high and exotic cars. I also provide towing for collisions and car accidents. I offer open and enclosed transport nationwide.

Target Market(s)

Car culture people high end auto collectors

Industry/Entity Type

Towing car carrier

Contact Information for Business Card

My company colors black yellow and silver

Font styles to use
Serif

```html
<!DOCTYPE html>
<html lang="en">
<head>
<meta charset="UTF-8">
<title>Vantro Business Cards</title>
<link href="https://fonts.googleapis.com/css2?family=Poppins:wght@400;600;700&display=swap" rel="stylesheet">
<style>
  :root {
    --backdrop: #1d1d1d;
    --card-white: #f4f4f4;
    --card-black: #0b0b0b;
    --brand-yellow: #f6d648;
    --ink: #1a1a1a;
    --rule: #b9b9b9;
    --white: #ffffff;
  }
  * { margin: 0; padding: 0; box-sizing: border-box; }
  html, body {
    width: 1200px; height: 900px; overflow: hidden;
    background: var(--backdrop);
    font-family: "Poppins", sans-serif;
  }
  .sheet {
    width: 1200px; height: 900px;
    display: flex; align-items: center; justify-content: center; gap: 40px;
  }
  .card {
    width: 530px; height: 303px; position: relative;
    box-shadow: 0 14px 30px rgba(0,0,0,0.55);
  }
  .card-front {
    background: var(--card-white);
    display: flex; align-items: center;
  }
  .front-brand {
    width: 255px; height: 100%;
    display: flex; align-items: center; justify-content: center; gap: 10px;
  }
  .brand-mark {
    width: 18px; height: 18px; background: var(--brand-yellow);
  }
  .brand-name {
    font-weight: 700; font-size: 40px; color: var(--ink); letter-spacing: 1px;
  }
  .divider {
    width: 1px; height: 150px; background: var(--rule);
  }
  .contact {
    padding-left: 24px; color: var(--ink);
  }
  .contact-name {
    font-weight: 700; font-size: 17px; color: var(--brand-yellow);
    text-transform: uppercase; letter-spacing: 0.5px; line-height: 1.1;
  }
  .contact-title {
    font-size: 13px; margin-bottom: 12px;
  }
  .contact-list { list-style: none; font-size: 12.5px; line-height: 1.5; }
  .contact-list li { display: flex; align-items: center; gap: 8px; }
  .contact-list svg { width: 11px; height: 11px; flex: none; }
  .contact-address {
    font-size: 12.5px; line-height: 1.35; margin-top: 10px;
  }
  .card-back {
    background: var(--card-black);
    display: flex; align-items: center; justify-content: center; gap: 12px;
  }
  .card-back .brand-name { color: var(--white); font-size: 46px; }
</style>
</head>
<body>
<main class="sheet">
  <section class="card card-front">
    <div class="front-brand">
      <span class="brand-mark"></span>
      <span class="brand-name">Vantro</span>
    </div>
    <div class="divider"></div>
    <div class="contact">
      <h1 class="contact-name">Marcus Hale</h1>
      <p class="contact-title">Managing Director</p>
      <ul class="contact-list">
        <li>
          <svg viewBox="0 0 12 12"><path d="M2.5 1 L4.5 1 L5.3 3.4 L4 4.4 Q5 6.8 7.6 8 L8.6 6.7 L11 7.5 L11 9.5 Q10.5 11 9 11 Q1 10 1 2.6 Q1 1 2.5 1 Z" fill="var(--brand-yellow)"/></svg>
          071-555 018 274
        </li>
        <li>
          <svg viewBox="0 0 12 12"><rect x="0.5" y="2" width="11" height="8" fill="var(--brand-yellow)"/><path d="M0.5 2 L6 6.5 L11.5 2" stroke="var(--white)" stroke-width="1" fill="none"/></svg>
          info@vantrohaul.com
        </li>
        <li>
          <svg viewBox="0 0 12 12"><circle cx="6" cy="6" r="5.2" fill="none" stroke="var(--brand-yellow)" stroke-width="1.2"/><ellipse cx="6" cy="6" rx="2.2" ry="5.2" fill="none" stroke="var(--brand-yellow)" stroke-width="1"/><line x1="0.8" y1="6" x2="11.2" y2="6" stroke="var(--brand-yellow)" stroke-width="1"/></svg>
          www.vantrohaul.com
        </li>
      </ul>
      <p class="contact-address">18 Harbor Lane, Suite 4<br>60817, Lakemont</p>
    </div>
  </section>

  <section class="card card-back">
    <span class="brand-mark"></span>
    <span class="brand-name">Vantro</span>
  </section>
</main>
</body>
</html>
```